Tech business card design

We need an amazing business card design for our new business 'Pexla' a marketing tech startup based in Sydney, Australia. We provide an online marketplace for businesses to search and buy advertising media, connect with service providers and learn more about marketing. We wish to communicate 'cool tech', reliability and professionalism and design based around our logo.

Target Market(s)

Business Owners

Contact Information for Business Card

Name
Position
Email Address
Website
Phone Number

Font styles to use
Other font styles liked:
• Avenir & Avenir Next

Colors

Designer to choose colors to be used in the design.

```html
<!DOCTYPE html>
<html lang="en">
<head>
<meta charset="utf-8">
<title>Pexla Business Card</title>
<link href="https://fonts.googleapis.com/css2?family=Nunito+Sans:wght@400;700;900&display=swap" rel="stylesheet">
<style>
  :root {
    --navy: #1b1f4d;
    --white: #ffffff;
    --swoosh: #8a8b90;
    --page: #e6e6e8;
    --mark-faint: #5e6188;
    --ink: #14163a;
  }
  * { margin: 0; padding: 0; box-sizing: border-box; }
  html, body { width: 1200px; height: 900px; overflow: hidden; }
  body {
    background: var(--page);
    font-family: "Nunito Sans", "Helvetica Neue", Arial, sans-serif;
    position: relative;
  }
  .card {
    position: absolute;
    width: 700px;
    height: 400px;
    border-radius: 28px;
    overflow: hidden;
    box-shadow: 0 10px 30px rgba(0,0,0,0.18);
  }
  .card-front { left: 110px; top: 40px; background: var(--white); }
  .card-back { left: 390px; top: 470px; background: var(--navy); }
  .front-shape { position: absolute; inset: 0; }
  .wordmark {
    position: absolute;
    left: 0; right: 0;
    top: 22px;
    text-align: center;
    font-weight: 900;
    font-size: 118px;
    line-height: 1;
    letter-spacing: -2px;
    color: var(--navy);
  }
  .tm { font-size: 16px; font-weight: 900; vertical-align: top; position: relative; top: 40px; margin-left: 4px; letter-spacing: 0; }
  .holder {
    position: absolute;
    left: 0; right: 0;
    top: 168px;
    text-align: center;
    color: var(--ink);
  }
  .holder-name { font-weight: 700; font-size: 19px; letter-spacing: 0.5px; }
  .holder-role { font-weight: 700; font-size: 14px; margin-top: 1px; }
  .contacts {
    position: absolute;
    left: 0; right: 0;
    top: 312px;
    display: flex;
    justify-content: center;
    gap: 26px;
    color: var(--white);
    font-size: 16px;
  }
  .contact-item { display: flex; align-items: center; gap: 6px; }
  .contact-item svg { width: 14px; height: 14px; fill: var(--white); }
  .address {
    position: absolute;
    left: 0; right: 0;
    top: 346px;
    text-align: center;
    color: var(--white);
    font-size: 16px;
  }
  .back-mark {
    position: absolute;
    left: 0; right: 0;
    top: 118px;
    text-align: center;
    font-weight: 900;
    font-size: 150px;
    line-height: 1;
    letter-spacing: -3px;
    color: var(--mark-faint);
  }
  .back-mark .tm { font-size: 18px; top: 50px; }
</style>
</head>
<body>
  <section class="card card-front">
    <svg class="front-shape" viewBox="0 0 700 400" aria-hidden="true">
      <path d="M0 262 Q 420 262 700 112 L700 400 L0 400 Z" fill="var(--navy)"/>
      <path d="M0 240 Q 430 252 690 130 Q 440 268 0 260 Z" fill="var(--swoosh)"/>
    </svg>
    <div class="wordmark">pexla<span class="tm">TM</span></div>
    <div class="holder">
      <div class="holder-name">JOHN SMITH</div>
      <div class="holder-role">Position</div>
    </div>
    <div class="contacts">
      <span class="contact-item">
        <svg viewBox="0 0 24 24"><path d="M6.6 10.8a15 15 0 0 0 6.6 6.6l2.2-2.2a1 1 0 0 1 1-.25 11.4 11.4 0 0 0 3.6.57 1 1 0 0 1 1 1V20a1 1 0 0 1-1 1A17 17 0 0 1 3 4a1 1 0 0 1 1-1h3.5a1 1 0 0 1 1 1c0 1.25.2 2.45.57 3.57a1 1 0 0 1-.25 1z"/></svg>
        012-345-6789
      </span>
      <span class="contact-item">
        <svg viewBox="0 0 24 24"><path d="M2 5h20v14H2z M2 5l10 8 10-8" fill="none" stroke="#fff" stroke-width="2.5"/></svg>
        info@pexla.com
      </span>
      <span class="contact-item">
        <svg viewBox="0 0 24 24"><circle cx="12" cy="12" r="9.5" fill="none" stroke="#fff" stroke-width="2"/><path d="M2.5 12h19M12 2.5c3 3 3 16 0 19M12 2.5c-3 3-3 16 0 19" fill="none" stroke="#fff" stroke-width="1.6"/></svg>
        www.pexla.com
      </span>
    </div>
    <div class="address">Street Name, City Name, Zipcode:012345</div>
  </section>

  <section class="card card-back">
    <div class="back-mark">pexla<span class="tm">TM</span></div>
  </section>
</body>
</html>
```